Luxury WordPress Website for CORALBASINS

I need a professional WordPress website for Coral Basins. The site should be modern, visually appealing, and user-friendly, reflecting the brand’s luxury and premium identity. It must include a homepage, product/service pages, contact form, and be responsive on both desktop and mobile devices. The design should allow for easy updates and integration of future content, while maintaining a polished and professional look.

Target Market(s)

swimmingpool & spa

Industry/Entity Type

Swimmingpool

Coding

Coded - Design and coding required

Font styles to use
Other font styles liked:
• HaboroSoft

Requirements
Must have
• Exclusive appearance
Nice to have
• • A logo that subtly incorporates water or pool elements. • A color palette that reflects luxury, elegance, and relaxation. • Clean and modern typography that is easy to read across all media. • Iconography or design elements that convey premium quality. • A versatile design that can be adapted for social media, merchandise, and promotional materials. • Optional: A tagline that emphasizes luxury and high-end pool experiences.

```html
<!DOCTYPE html>
<html lang="en">
<head>
<meta charset="utf-8">
<title>Coral Basins — Design. Build. Enjoy.</title>
<link href="https://fonts.googleapis.com/css2?family=Poppins:wght@400;500;600;700;800&display=swap" rel="stylesheet">
<style>
:root{
  --blue:#1a7fd4;
  --blue-deep:#0d5fae;
  --navy:#0b2a40;
  --ink:#1c2b36;
  --muted:#4a5560;
  --bg:#eaf8fc;
  --white:#ffffff;
  --footer:#0a1822;
}
*{margin:0;padding:0;box-sizing:border-box}
html,body{width:1200px;height:5017px;overflow:hidden}
body{font-family:'Poppins',sans-serif;background:var(--bg);color:var(--ink)}
.page{position:relative;width:1200px;height:5017px;overflow:hidden;background:var(--bg)}
.abs{position:absolute}
.photo{position:absolute;overflow:hidden}

/* header */
.site-header{position:absolute;top:0;left:0;width:1200px;height:80px;background:var(--white);z-index:5}
.brand-tab{position:absolute;left:111px;top:0;width:195px;height:191px;background:var(--white);z-index:6;display:flex;flex-direction:column;align-items:center;justify-content:center;gap:10px;box-shadow:0 4px 14px rgba(0,0,0,.12)}
.brand-dot{width:56px;height:56px;border-radius:50%;background:var(--blue)}
.brand-name{font-weight:800;font-size:17px;color:var(--navy);letter-spacing:.5px}
.brand-tag{font-size:8px;font-weight:600;color:var(--navy);margin-top:-8px}
.nav{position:absolute;top:30px;font-size:15px;font-weight:500;color:var(--ink)}
.nav.active{color:var(--blue)}
.call-circle{position:absolute;left:932px;top:16px;width:50px;height:50px;border-radius:50%;background:var(--navy);border:3px solid var(--blue)}
.call-box{position:absolute;left:960px;top:14px;width:240px;height:52px;background:var(--blue);border-radius:0;z-index:-1}
.call-label{position:absolute;left:999px;top:20px;font-size:10px;font-weight:500;color:var(--white)}
.call-num{position:absolute;left:999px;top:34px;font-size:19px;font-weight:500;color:var(--white)}

/* hero */
.hero{position:absolute;top:80px;left:0;width:1200px;height:730px;background:linear-gradient(180deg,#3a3550 0%,#8a5a48 35%,#e39a4c 55%,#5a4a48 75%,#1d2a38 100%)}
.hero-kicker{position:absolute;left:111px;top:288px;font-size:19px;font-weight:500;color:var(--white)}
.hero-title{position:absolute;left:111px;top:316px;font-size:60px;font-weight:800;line-height:64px;color:var(--white)}
.hero-text{position:absolute;left:111px;top:455px;font-size:20px;line-height:31px;color:var(--white)}
.btn{position:absolute;display:flex;align-items:center;justify-content:center;border-radius:24px;font-weight:600;font-size:15px}
.btn-blue{background:var(--blue);color:var(--white)}
.btn-white{background:var(--white);color:var(--blue)}
.btn-navy{background:var(--navy);color:var(--white)}

.section-title{position:absolute;left:0;width:1200px;text-align:center;font-size:42px;font-weight:700;color:var(--navy);letter-spacing:-.5px}
.section-title .hl{color:var(--blue)}
.lead{position:absolute;text-align:center;font-size:15px;line-height:30px;color:var(--muted)}

/* testimonial */
.quote-card{position:absolute;left:169px;top:1182px;width:384px;height:328px;background:var(--white);border-radius:22px;box-shadow:0 8px 30px rgba(20,60,90,.10);padding:34px 38px}
.quote-marks{display:flex;gap:4px;margin-bottom:28px}
.quote-marks span{width:30px;height:30px;border-radius:50%;background:#cfe6f6}
.quote-card p{font-size:13.5px;line-height:26px;color:var(--muted);margin-bottom:25px}
.quote-name{font-size:13.5px;font-weight:600;color:var(--blue)}

/* signature cards */
.pool-card{position:absolute;top:2433px;width:233px;height:366px;background:var(--white);border:2px solid #cfe4f4;border-radius:18px;overflow:hidden;text-align:center}
.pool-card .photo{left:0;top:0;width:100%;height:240px}
.pool-card h3{position:absolute;top:260px;width:100%;font-size:16px;font-weight:700;color:var(--blue)}
.pool-card p{position:absolute;top:286px;left:14px;right:14px;font-size:13.5px;line-height:22px;color:var(--muted)}
.pool-card.featured{background:var(--blue);border-color:var(--blue)}
.pool-card.featured h3,.pool-card.featured p{color:var(--white)}

/* before/after */
.ba-pair{position:absolute;top:3978px;width:483px;height:325px;border-radius:18px;overflow:hidden;box-shadow:0 14px 20px rgba(0,0,0,.12)}
.ba-pair .photo{top:0;height:325px;width:241px}
.ba-label{position:absolute;top:4248px;width:130px;height:30px;border-radius:15px;font-size:12px;font-weight:700;color:var(--white);display:flex;align-items:center;justify-content:center}
.ba-label.before{background:var(--blue)}
.ba-label.after{background:var(--navy)}

/* footer */
.footer-name{position:absolute;left:111px;top:4786px;width:250px;text-align:center;font-size:23px;font-weight:800;color:var(--white)}
.footer-tag{position:absolute;left:111px;top:4818px;width:250px;text-align:center;font-size:10px;color:var(--white)}
.footer-head{position:absolute;top:4686px;font-size:17px;font-weight:700;color:var(--blue)}
.footer-item{position:absolute;font-size:15px;color:var(--white)}
.social{position:absolute;top:4692px;width:34px;height:34px;border-radius:50%;background:var(--white);display:flex;align-items:center;justify-content:center}
.social span{width:12px;height:12px;border-radius:50%;background:var(--blue)}
</style>
</head>
<body>
<div class="page">

  <!-- header -->
  <header class="site-header">
    <span class="nav active" style="left:389px">Home</span>
    <span class="nav" style="left:475px">About Us</span>
    <span class="nav" style="left:587px">Services</span>
    <span class="nav" style="left:692px">Products</span>
    <span class="nav" style="left:802px">Contact Us</span>
    <div class="call-box"></div>
    <div class="call-circle">
      <svg width="44" height="44" viewBox="0 0 44 44"><path d="M15 13c2-1 3 0 4 3l1 2c0 1-1 2-2 3 1 3 3 5 6 6 1-1 2-2 3-2l2 1c3 1 4 2 3 4-1 2-3 3-5 2-6-2-10-6-12-12-1-2 0-6 0-7z" fill="#fff"/></svg>
    </div>
    <span class="call-label">CALL US:</span>
    <span class="call-num">+1 555 014 2290</span>
  </header>
  <div class="brand-tab">
    <div class="brand-dot"></div>
    <div class="brand-name">CORAL BASINS</div>
    <div class="brand-tag">ALL YOUR DREAMS COME TRUE</div>
  </div>

  <!-- hero -->
  <section class="hero" role="img" aria-label="Resort pool at sunset framed by palm trees and cabanas">
  </section>
  <div class="hero-kicker">CORAL BASINS</div>
  <h1 class="hero-title">DESIGN.<br>BUILD. ENJOY.</h1>
  <p class="hero-text">Exclusive pools and bespoke installations,<br>crafted for the way you live.</p>
  <a class="btn btn-blue" style="left:111px;top:539px;width:244px;height:44px">Request a Consultation</a>
  <a class="btn btn-white" style="left:378px;top:539px;width:197px;height:44px">Explore Our Pools</a>

  <svg class="abs" style="left:0;top:620px" width="1200" height="200" viewBox="0 0 1200 200" preserveAspectRatio="none">
    <path d="M0 110 C200 40 420 60 600 120 C800 180 1000 130 1200 40 L1200 200 L0 200Z" fill="#0b2a40"/>
    <path d="M0 135 C220 70 420 90 600 140 C820 200 1010 150 1200 70 L1200 200 L0 200Z" fill="#1a7fd4"/>
    <path d="M0 160 C230 110 430 120 620 170 C820 210 1020 170 1200 110 L1200 200 L0 200Z" fill="#eaf8fc"/>
    <path d="M0 175 L0 200 L1200 200 L1200 140 C1000 190 780 200 600 188 C400 170 200 150 0 175Z" fill="#eaf8fc"/>
  </svg>

  <!-- intro -->
  <div class="abs" style="left:576px;top:860px;width:48px;height:48px;border-radius:50%;background:var(--blue)"></div>
  <h2 class="section-title" style="top:956px"><span class="hl">WHERE DESIGN</span> MEETS PERFECTION</h2>
  <p class="lead" style="left:210px;top:1022px;width:780px">At Coral Basins, we don't just build pools — we create personal sanctuaries. Each project is a testament to refined craftsmanship, cutting-edge engineering, and artistic vision. From concept to completion, our team ensures every detail exceeds expectations, delivering pools that are as enduring as they are beautiful.</p>

  <div class="quote-card">
    <div class="quote-marks"><span></span><span></span></div>
    <p>Our Coral Basins pool turned our backyard into a resort. Every guest is in awe — truly a masterpiece!</p>
    <p>Professional, responsive, &amp; creative. The design process was seamless, &amp; the result is perfection.</p>
    <div class="quote-name">Elena R., Laguna Beach</div>
  </div>
  <div class="photo" style="left:500px;top:1245px;width:531px;height:345px;border-radius:22px;background:linear-gradient(180deg,#1c2a6a 0%,#2b4aa0 45%,#1f64b8 70%,#0e2f70 100%);box-shadow:0 16px 26px rgba(0,0,0,.18)" role="img" aria-label="Rooftop infinity pool lit at night overlooking a city skyline"></div>

  <!-- video band -->
  <div class="photo" style="left:0;top:1708px;width:1200px;height:513px;background:linear-gradient(180deg,#d9e4ea 0%,#c6d6dc 30%,#6fc3dc 50%,#2da7cf 75%,#d8c0a5 90%,#cfb394 100%)" role="img" aria-label="Video still of a modern courtyard pool with potted trees"></div>
  <div class="abs" style="left:541px;top:1900px;width:118px;height:118px;border-radius:50%;background:rgba(255,255,255,.35)"></div>
  <div class="abs" style="left:564px;top:1923px;width:72px;height:72px;border-radius:50%;background:var(--white)"></div>
  <div class="abs" style="left:573px;top:1932px;width:54px;height:54px;border-radius:50%;background:var(--blue)"></div>
  <svg class="abs" style="left:590px;top:1947px" width="24" height="24" viewBox="0 0 24 24"><path d="M4 2 L22 12 L4 22Z" fill="#fff"/></svg>

  <!-- signature pools -->
  <h2 class="section-title" style="top:2280px"><span class="hl">OUR SIGNATURE</span> POOLS</h2>
  <p class="lead" style="left:250px;top:2337px;width:700px;font-size:14.5px;line-height:26px">Sed ut perspiciatis unde omnis iste natus error sit voluptatem accusantium doloremque laudantium, totam rem aperiam, eaque ipsa quae ab illo inventore verit</p>

  <article class="pool-card" style="left:111px">
    <div class="photo" style="background:linear-gradient(180deg,#1b3a7a,#3d7fc0 55%,#1aa3c8)" role="img" aria-label="Infinity pool on a cliffside villa at dusk"></div>
    <h3>INFINITY SERIES</h3>
    <p>For those who desire endless horizons &amp; breathtaking design</p>
  </article>
  <article class="pool-card featured" style="left:360px">
    <div class="photo" style="background:linear-gradient(180deg,#6b86a6,#8a7a68 45%,#3fb0c4)" role="img" aria-label="Resort-style pool terrace with spa at sunset"></div>
    <h3>RESORT COLLECTION</h3>
    <p>Transform your home into a private paradise.</p>
  </article>
  <article class="pool-card" style="left:608px">
    <div class="photo" style="background:linear-gradient(180deg,#9fb4c6,#c9cdd0 45%,#4aa6cf)" role="img" aria-label="Modern architectural house with a rectangular pool"></div>
    <h3>ARCHITECTURAL POOLS</h3>
    <p>Minimalist lines, advanced technology, pure luxury.</p>
  </article>
  <article class="pool-card" style="left:855px">
    <div class="photo" style="background:linear-gradient(180deg,#8fc7d8,#2a9fc2 50%,#39c3c6)" role="img" aria-label="Custom glass-walled pool overlooking the ocean"></div>
    <h3>CUSTOM CONCEPTS</h3>
    <p>Tailored creations designed around your vision and lifestyle.</p>
  </article>
  <a class="btn btn-blue" style="left:493px;top:2840px;width:214px;height:43px">View All Collections</a>

  <!-- ready section -->
  <svg class="abs" style="left:0;top:2880px" width="1200" height="170" viewBox="0 0 1200 170" preserveAspectRatio="none">
    <path d="M0 60 C250 120 450 20 700 40 C900 55 1050 30 1200 0 L1200 170 L0 170Z" fill="#d7eef8"/>
    <path d="M0 90 C260 150 460 60 700 80 C900 100 1060 80 1200 50 L1200 170 L0 170Z" fill="#f3fbfe"/>
  </svg>
  <div class="abs" style="left:0;top:3050px;width:1200px;height:750px;background:#f3fbfe"></div>
  <div class="photo" style="left:-40px;top:3088px;width:585px;height:585px;border-radius:50%;background:linear-gradient(180deg,#8ec8ee 0%,#cfd7dc 40%,#8fa69a 60%,#2aa3d8 80%,#1a8fd0 100%)" role="img" aria-label="Mediterranean villa with a backyard pool"></div>
  <div class="photo" style="left:249px;top:3375px;width:352px;height:352px;border-radius:50%;border:6px solid #fff;background:linear-gradient(180deg,#2a3a5a 0%,#6a5a4a 45%,#c08a4a 60%,#1c5f9a 100%)" role="img" aria-label="Modern pavilion with pool lit at twilight"></div>

  <h2 class="section-title" style="left:640px;width:474px;top:3222px;line-height:50px"><span class="hl">WE'RE READY</span> WHEN<br>YOU ARE</h2>
  <p class="lead" style="left:650px;top:3342px;width:455px;font-size:14.5px;line-height:26px">Whether you're ready to build, explore design ideas, or just curious about what's possible — our team is here to help. Reach out today and let's bring your vision to life.</p>
  <p class="lead" style="left:650px;top:3446px;width:455px;font-size:14.5px;line-height:26px">Sed ut perspiciatis unde omnis iste natus error sit voluptatem accusantium doloremque laudantium, totam rem aperiam, eaque ipsa quae ab illo</p>
  <a class="btn btn-blue" style="left:738px;top:3551px;width:276px;height:44px">Schedule Your Consultation</a>
  <a class="btn btn-navy" style="left:738px;top:3615px;width:276px;height:44px">Call Us: +1 555 014 2290</a>

  <!-- inspiration -->
  <h2 class="section-title" style="top:3826px"><span class="hl">DIVE INTO</span> INSPIRATION</h2>
  <p class="lead" style="left:250px;top:3883px;width:700px;font-size:14.5px;line-height:26px">Sed ut perspiciatis unde omnis iste natus error sit voluptatem accusantium doloremque laudantium, totam rem aperiam, eaque ipsa quae ab illo inventore verit</p>

  <div class="ba-pair" style="left:111px">
    <div class="photo" style="left:0;background:linear-gradient(180deg,#9aa2a6,#c8cccd 50%,#8a8f90)" role="img" aria-label="Concrete pool shell under construction"></div>
    <div class="photo" style="left:242px;background:linear-gradient(180deg,#4a6a3a,#8a5a3a 35%,#1e8fd6 55%,#b8b0a2)" role="img" aria-label="Finished pool with stone paving in a garden"></div>
  </div>
  <div class="ba-pair" style="left:606px">
    <div class="photo" style="left:0;background:linear-gradient(180deg,#7a6a5a,#a87a58 50%,#6a5a4a)" role="img" aria-label="Excavated site with steel rebar framing"></div>
    <div class="photo" style="left:242px;background:linear-gradient(180deg,#c9b9a6,#5ab8c8 35%,#3aa8c0 80%,#c9b9a6)" role="img" aria-label="Completed pool with tiled steps"></div>
  </div>
  <div class="ba-label before" style="left:166px">BEFORE</div>
  <div class="ba-label after" style="left:409px">AFTER</div>
  <div class="ba-label before" style="left:660px">BEFORE</div>
  <div class="ba-label after" style="left:903px">AFTER</div>
  <div class="abs" style="left:563px;top:4338px;width:32px;height:32px;border-radius:50%;background:#7dc0ec"></div>
  <div class="abs" style="left:602px;top:4338px;width:32px;height:32px;border-radius:50%;background:var(--blue)"></div>
  <svg class="abs" style="left:563px;top:4338px" width="71" height="32" viewBox="0 0 71 32"><path d="M19 11 L14 16 L19 21" stroke="#fff" stroke-width="2" fill="none"/><path d="M52 11 L57 16 L52 21" stroke="#fff" stroke-width="2" fill="none"/></svg>

  <!-- footer -->
  <svg class="abs" style="left:0;top:4410px" width="1200" height="220" viewBox="0 0 1200 220" preserveAspectRatio="none">
    <path d="M0 40 C200 0 420 70 650 110 C880 150 1060 90 1200 30 L1200 220 L0 220Z" fill="#0b2a40"/>
    <path d="M0 90 C220 50 430 110 660 140 C880 170 1060 120 1200 70 L1200 220 L0 220Z" fill="#1a7fd4"/>
    <path d="M0 130 C230 100 440 150 670 170 C890 190 1060 160 1200 120 L1200 220 L0 220Z" fill="#0a1822"/>
  </svg>
  <div class="abs" style="left:0;top:4620px;width:1200px;height:397px;background:var(--footer)"></div>

  <div class="abs" style="left:196px;top:4680px;width:80px;height:80px;border-radius:50%;background:var(--white)"></div>
  <div class="footer-name">CORAL BASINS</div>
  <div class="footer-tag">ALL YOUR DREAMS COME TRUE</div>

  <div class="footer-head" style="left:436px">QUICK LINKS</div>
  <div class="footer-item" style="left:442px;top:4729px">»&nbsp;&nbsp;&nbsp;&nbsp;Home</div>
  <div class="footer-item" style="left:442px;top:4766px">»&nbsp;&nbsp;&nbsp;&nbsp;About Us</div>
  <div class="footer-item" style="left:442px;top:4803px">»&nbsp;&nbsp;&nbsp;&nbsp;Our Products</div>
  <div class="footer-item" style="left:442px;top:4840px">»&nbsp;&nbsp;&nbsp;&nbsp;Services</div>
  <div class="footer-item" style="left:442px;top:4877px">»&nbsp;&nbsp;&nbsp;&nbsp;Contact Us</div>

  <div class="footer-head" style="left:653px">CONTACT INFO</div>
  <svg class="abs" style="left:655px;top:4733px" width="12" height="16" viewBox="0 0 12 16"><path d="M6 0C3 0 0 2.5 0 6c0 4 6 10 6 10s6-6 6-10c0-3.5-3-6-6-6zm0 8.5A2.5 2.5 0 1 1 6 3.5a2.5 2.5 0 0 1 0 5z" fill="#fff"/></svg>
  <div class="footer-item" style="left:684px;top:4729px;line-height:37px">48 Harborlight Avenue,<br>Naples, FL 34102</div>
  <svg class="abs" style="left:654px;top:4845px" width="14" height="14" viewBox="0 0 14 14"><path d="M3 0l2 3-1.5 1.5c1 2 3 4 5 5L10 8l3 2-1 3c-6 0-12-6-12-12z" fill="#fff"/></svg>
  <div class="footer-item" style="left:684px;top:4840px">+1 555 014 2290</div>
  <svg class="abs" style="left:654px;top:4883px" width="14" height="11" viewBox="0 0 14 11"><rect width="14" height="11" rx="1" fill="#fff"/><path d="M0 1 L7 6 L14 1" stroke="#0a1822" stroke-width="1.3" fill="none"/></svg>
  <div class="footer-item" style="left:684px;top:4877px">hello@coralbasins.com</div>

  <div class="social" style="left:932px"><span></span></div>
  <div class="social" style="left:972px"><span></span></div>
  <div class="social" style="left:1012px"><span></span></div>
  <div class="social" style="left:1052px"><span></span></div>

  <a class="btn btn-white" style="left:968px;top:4908px;width:120px;height:40px;font-size:12px;gap:8px">
    <svg width="12" height="8" viewBox="0 0 12 8"><path d="M1 7 L6 2 L11 7" stroke="#1a7fd4" stroke-width="2" fill="none"/></svg>GO TOP</a>
  <div class="abs" style="left:111px;top:4949px;width:850px;border-top:1px dashed rgba(255,255,255,.35)"></div>
  <div class="abs" style="left:0;top:4974px;width:1200px;text-align:center;font-size:14px;color:var(--white)">(C) COPYRIGHT 2025 | ALL RIGHTS RESERVED</div>

</div>
</body>
</html>
```